Card Design for my dog training business Brightpaw Obedience

Need a business card design for my dog training business with my new logo. Want the card to come off professional yet fun. Want it to be very eye catchy as well. I normally have these at vet clinics, pet stores, and groomers. so need it to look better than my competitors.
Target Market(s)
dog owners
Industry/Entity Type
Dog Training
Contact Information for Business Card
needs logo, my name and info
Font styles to use
Serif
Colors
0255a3
ffffff
ec1f27
000000
333333
fbfbfb
Requirements
Must have
- Brightpaw Obedience
- Felix Orland
- 415 903 2276
- info@brightpawobedience.example
- www.brightpawobedience.example

```html
<!DOCTYPE html>
<html lang="en">
<head>
<meta charset="utf-8">
<title>Brightpaw Obedience — Business Card</title>
<link href="https://fonts.googleapis.com/css2?family=Noto+Serif:wght@400;700&display=swap" rel="stylesheet">
<style>
  :root {
    --backdrop: #3a322e;
    --card-black: #111111;
    --card-black-soft: #262626;
    --card-white: #fbfbfb;
    --ink: #000000;
    --ink-soft: #333333;
    --silver-light: #e6e6e6;
    --silver-dark: #5a5a5a;
    --white: #ffffff;
  }
  * { box-sizing: border-box; margin: 0; padding: 0; }
  html, body { width: 1200px; height: 900px; overflow: hidden; }
  body {
    background: var(--backdrop);
    font-family: "Noto Serif", Georgia, serif;
    position: relative;
  }
  .card {
    position: absolute;
    width: 525px;
    height: 300px;
    top: 300px;
    overflow: hidden;
    border-radius: 4px;
    box-shadow: 0 10px 28px rgba(0,0,0,0.45);
  }

  /* Front */
  .card-front {
    left: 40px;
    background: linear-gradient(160deg, var(--card-black-soft), var(--card-black) 60%);
    color: var(--white);
  }
  .dog-artwork {
    position: absolute;
    left: 0; top: 0;
    width: 255px; height: 250px;
    background: radial-gradient(ellipse at 45% 55%, var(--silver-light), var(--silver-dark) 45%, rgba(17,17,17,0) 72%);
    opacity: 0.85;
  }
  .front-brand {
    position: absolute;
    left: 270px; top: 78px;
    width: 225px;
    text-align: center;
  }
  .front-brand .rule { height: 2px; background: var(--white); }
  .front-brand .brand-name {
    font-size: 30px;
    font-weight: 400;
    line-height: 1.15;
    letter-spacing: 1px;
    padding: 10px 0 8px;
  }
  .front-web {
    position: absolute;
    right: 28px; bottom: 58px;
    font-size: 15px;
  }
  .front-line {
    position: absolute;
    left: 0; right: 0; bottom: 44px;
    height: 2px;
    background: var(--silver-light);
  }

  /* Back */
  .card-back {
    left: 635px;
    background: var(--card-white);
    color: var(--ink);
  }
  .holder {
    position: absolute;
    left: 30px; top: 30px;
    width: 300px;
  }
  .holder-name { font-size: 20px; font-weight: 700; line-height: 1.2; }
  .holder-company { font-size: 13px; color: var(--ink-soft); }
  .holder-rule { height: 1px; background: var(--ink); margin-top: 8px; }
  .contact-list {
    position: absolute;
    left: 30px; top: 100px;
    list-style: none;
    font-size: 13px;
    color: var(--ink-soft);
  }
  .contact-list li { display: flex; align-items: center; gap: 8px; margin-bottom: 6px; }
  .contact-list svg { width: 13px; height: 13px; fill: var(--ink); }
  .back-brand {
    position: absolute;
    right: 30px; top: 40px;
    display: flex; align-items: center; gap: 8px;
    font-size: 16px;
    color: var(--ink);
  }
  .back-brand .mark {
    width: 14px; height: 14px;
    border-radius: 50%;
    background: var(--ink);
  }
  .tagline-rule {
    position: absolute;
    left: 190px; right: 30px; top: 160px;
    height: 1px; background: var(--ink);
  }
  .tagline {
    position: absolute;
    right: 30px; top: 170px;
    text-align: right;
    font-size: 14px;
    line-height: 1.4;
    color: var(--ink-soft);
  }
  .web-band {
    position: absolute;
    left: 0; right: 0; bottom: 0;
    height: 54px;
    background: var(--card-black);
    color: var(--white);
    display: flex; align-items: center; justify-content: flex-end;
    padding-right: 30px;
    font-size: 15px;
  }
</style>
</head>
<body>

  <section class="card card-front">
    <div class="dog-artwork" role="img" aria-label="Silver foil illustration of two dog heads"></div>
    <div class="front-brand">
      <div class="rule"></div>
      <div class="brand-name">Brightpaw<br>Obedience</div>
      <div class="rule"></div>
    </div>
    <div class="front-web">www.brightpawobedience.example</div>
    <div class="front-line"></div>
  </section>

  <section class="card card-back">
    <div class="holder">
      <div class="holder-name">Felix Orland</div>
      <div class="holder-company">Brightpaw Obedience</div>
      <div class="holder-rule"></div>
    </div>
    <ul class="contact-list">
      <li>
        <svg viewBox="0 0 24 24" aria-hidden="true"><path d="M6.6 10.8a15 15 0 0 0 6.6 6.6l2.2-2.2a1 1 0 0 1 1-.25 11.4 11.4 0 0 0 3.6.57 1 1 0 0 1 1 1V20a1 1 0 0 1-1 1A17 17 0 0 1 3 4a1 1 0 0 1 1-1h3.5a1 1 0 0 1 1 1c0 1.25.2 2.45.57 3.57a1 1 0 0 1-.25 1z"/></svg>
        415 903 2276
      </li>
      <li>
        <svg viewBox="0 0 24 24" aria-hidden="true"><path d="M2 5h20v14H2z M2 5l10 8 10-8" stroke="#fbfbfb" stroke-width="1.5"/></svg>
        info@brightpawobedience.example
      </li>
    </ul>
    <div class="back-brand"><span class="mark"></span>Brightpaw Obedience</div>
    <div class="tagline-rule"></div>
    <p class="tagline">“Building better manners<br>one good dog at a time.”</p>
    <div class="web-band">www.brightpawobedience.example</div>
  </section>

</body>
</html>
```